Northfield Builders Guild Business card

We are looking for a new business card design with photo included.
Our business is a nonprofit construction contractor membership organization. We offer business education, assist with business setup and licensing, provide safety training, and provide a member directory.
URL: www.builderslinkguild.org
Color code:
CMYK: 0 cyan, 42 magenta, 100 yellow, 0 black for Print.
Hexidecimal: #FF9900
RGB: R 255; G 153; B 0

```html
<!DOCTYPE html>
<html lang="en">
<head>
<meta charset="utf-8">
<title>Northfield Builders Guild – Business Card</title>
<link href="https://fonts.googleapis.com/css2?family=Montserrat:wght@400;500;700;900&display=swap" rel="stylesheet">
<style>
  :root {
    --orange: #ff9900;
    --orange-deep: #f08c0a;
    --ink: #2e2e2e;
    --paper: #ffffff;
    --paper-shade: #efefef;
    --stage: #d9d6d1;
    --shirt: #2456b8;
  }
  * { margin: 0; padding: 0; box-sizing: border-box; }
  html, body { width: 1200px; height: 985px; overflow: hidden; }
  body {
    background: var(--stage);
    font-family: "Montserrat", sans-serif;
    position: relative;
  }
  .card {
    position: absolute;
    width: 640px;
    height: 366px;
    overflow: hidden;
    box-shadow: 0 6px 18px rgba(0,0,0,.25);
  }
  /* Front */
  .card-front {
    left: 420px; top: 80px;
    background: linear-gradient(160deg, var(--orange-deep), var(--orange));
    display: flex; align-items: center; justify-content: center;
  }
  .front-name {
    font-weight: 900;
    color: var(--ink);
    font-size: 70px;
    line-height: 1;
    text-transform: uppercase;
    text-align: center;
    letter-spacing: -1px;
  }
  /* Back */
  .card-back {
    left: 160px; top: 520px;
    background: linear-gradient(180deg, var(--paper), var(--paper-shade));
  }
  .card-art { position: absolute; inset: 0; }
  .brand-name {
    position: absolute; left: 30px; top: 26px;
    font-weight: 900; font-size: 20px; color: var(--ink);
    text-transform: uppercase; letter-spacing: -0.3px;
    white-space: nowrap;
  }
  .person { position: absolute; left: 30px; top: 74px; }
  .person-name { font-size: 27px; font-weight: 700; color: var(--ink); line-height: 1.2; }
  .person-name .first { color: var(--orange); }
  .person-title { font-size: 20px; font-weight: 500; color: var(--ink); margin-top: 2px; }
  .contacts { position: absolute; left: 30px; top: 170px; list-style: none; }
  .contacts li {
    display: flex; align-items: center; gap: 10px;
    font-size: 16.5px; color: var(--ink); height: 29px;
    white-space: nowrap;
  }
  .contacts svg { width: 16px; height: 16px; fill: var(--orange); flex: none; }
  .address {
    position: absolute; left: 0; right: 0; bottom: 0; height: 52px;
    display: flex; align-items: center; padding-left: 80px;
    font-size: 17px; font-weight: 500; color: var(--ink);
    white-space: nowrap;
  }
</style>
</head>
<body>

<section class="card card-front">
  <h1 class="front-name">Northfield<br>Builders<br>Guild</h1>
</section>

<section class="card card-back">
  <svg class="card-art" viewBox="0 0 640 366" width="640" height="366">
    <defs>
      <linearGradient id="portraitTone" x1="0" y1="0" x2="0" y2="1">
        <stop offset="0" stop-color="#f29412"/>
        <stop offset="0.5" stop-color="#f29412"/>
        <stop offset="0.68" stop-color="#3a5fae"/>
        <stop offset="1" stop-color="#2456b8"/>
      </linearGradient>
    </defs>
    <circle cx="760" cy="330" r="376" fill="url(#portraitTone)" stroke="#2e2e2e" stroke-width="4"
            role="img" aria-label="Portrait photo of the inspector in a blue polo shirt on an orange background"/>
    <rect x="0" y="312" width="640" height="54" fill="#ff9900"/>
    <rect x="0" y="310" width="640" height="4" fill="#2e2e2e"/>
  </svg>

  <div class="brand-name">Northfield Builders Guild</div>

  <div class="person">
    <div class="person-name"><span class="first">Dale</span> Moreno</div>
    <div class="person-title">Certified Mold Inspector</div>
  </div>

  <ul class="contacts">
    <li><svg viewBox="0 0 24 24"><path d="M6.6 10.8a15.1 15.1 0 0 0 6.6 6.6l2.2-2.2a1 1 0 0 1 1-.25 11.4 11.4 0 0 0 3.6.57 1 1 0 0 1 1 1V20a1 1 0 0 1-1 1A17 17 0 0 1 3 4a1 1 0 0 1 1-1h3.5a1 1 0 0 1 1 1c0 1.25.2 2.45.57 3.57a1 1 0 0 1-.25 1z"/></svg>(555) 210-4837 (Office)</li>
    <li><svg viewBox="0 0 24 24"><path d="M7 3h10v4H7zM4 8h16a2 2 0 0 1 2 2v6h-4v5H6v-5H2v-6a2 2 0 0 1 2-2zm4 8v3h8v-3z"/></svg>555.310.2246 (Fax)</li>
    <li><svg viewBox="0 0 24 24"><path d="M2 5h20v14H2zm2 2v.5l8 5 8-5V7l-8 5z"/></svg>support@nbguild.org</li>
    <li><svg viewBox="0 0 24 24"><circle cx="12" cy="12" r="10"/></svg>www.builderslinkguild.org</li>
  </ul>

  <div class="address">4820 Linden Ridge Rd., Suite #100 Fairview, OR 97000</div>
</section>

</body>
</html>
```